Business Cards Design for the electrical wholesaler: clean bold dynamic :)

We need a business card design that would follow our latest brand guidelines. As an electrical wholesaler we want to bring a fresh look and feel into the industry. The design should be clean bold and dynamic. It should come alive with the renewed energy of our green colour. Our grey colour should keep things balanced and complement the notion of maturity and responsibility. We employ Lato as a corporate font however are not bound by this font and we’re open to interpretation here.

Target Market(s)

Electrical contractors

Industry/Entity Type

Business

Contact Information for Business Card

Logo
Name & Surname: Halyna Dorosh
Job Title: Director of Marketing
Email: halya.dorosh@quillmail.example
Cell phone: XXX.XXX.XXXX
Address: 20517 - 87 Ave. Edmonton, AB, Canada. T6K 4N8
Business Phone: 780.555.0184
Website: www.brovix.example

Font styles to use
Other font styles liked:
• Lato

Requirements
Must have
• Logo & website
Nice to have
• Brand elements - some of them you may find in the attached Brand Guidelines (e.g. three lines on the background signifying "W")

```html
<!DOCTYPE html>
<html lang="en">
<head>
<meta charset="utf-8">
<title>Brovix Business Card</title>
<link rel="stylesheet" href="https://fonts.googleapis.com/css2?family=Exo+2:wght@600&family=Roboto:wght@400;500&display=swap">
<style>
  :root {
    --page-bg: #e6e3df;
    --card-bg: #f4f4f2;
    --card-edge: #d8d8d6;
    --band-grey: #4b4c4d;
    --brand-grey: #4a4b4d;
    --brand-green: #7cc242;
    --text-light: #dcdcdc;
    --text-dark: #4a4b4d;
  }
  * { margin: 0; padding: 0; box-sizing: border-box; }
  html, body {
    width: 1200px;
    height: 1054px;
    overflow: hidden;
    background: var(--page-bg);
    font-family: "Roboto", Arial, sans-serif;
  }
  .card {
    position: absolute;
    left: 100px;
    top: 225px;
    width: 1000px;
    height: 604px;
    background: var(--card-bg);
    border: 1px solid var(--card-edge);
    border-radius: 4px;
    box-shadow: 0 8px 24px rgba(0,0,0,0.12);
    overflow: hidden;
  }
  .brand {
    position: absolute;
    left: 58px;
    top: 70px;
    display: flex;
    align-items: center;
    gap: 20px;
  }
  .brand-mark {
    width: 34px;
    height: 34px;
    background: var(--brand-green);
  }
  .brand-name {
    font-family: "Roboto", Arial, sans-serif;
    font-weight: 500;
    font-size: 92px;
    line-height: 1;
    color: var(--brand-grey);
    letter-spacing: -1px;
  }
  .info-band {
    position: absolute;
    left: 0;
    top: 238px;
    width: 100%;
    height: 264px;
    background: var(--band-grey);
  }
  .person-name {
    position: absolute;
    left: 58px;
    top: 38px;
    font-family: "Exo 2", "Roboto", sans-serif;
    font-weight: 600;
    font-size: 42px;
    color: var(--brand-green);
  }
  .person-title {
    position: absolute;
    left: 58px;
    top: 96px;
    font-size: 24px;
    color: var(--text-light);
  }
  .contacts {
    position: absolute;
    left: 58px;
    top: 155px;
    font-size: 24px;
    color: var(--text-light);
  }
  .contact-row {
    display: flex;
    align-items: center;
    gap: 12px;
    height: 36px;
  }
  .contact-item { display: flex; align-items: center; gap: 12px; white-space: nowrap; }
  .contact-item + .contact-item { margin-left: 6px; }
  .icon { width: 26px; height: 26px; flex: none; }
  .accent { color: var(--brand-green); }
  .address {
    position: absolute;
    left: 58px;
    top: 538px;
    font-size: 24px;
    color: var(--text-dark);
  }
</style>
</head>
<body>
  <div class="card">
    <div class="brand">
      <span class="brand-mark"></span>
      <span class="brand-name">brovix</span>
    </div>

    <div class="info-band">
      <div class="person-name">Halyna Dorosh</div>
      <div class="person-title">Director of Marketing</div>
      <div class="contacts">
        <div class="contact-row">
          <div class="contact-item">
            <svg class="icon" viewBox="0 0 26 26" aria-hidden="true">
              <circle cx="13" cy="13" r="12" fill="none" stroke="#7cc242" stroke-width="2"/>
              <path d="M8 9c0 5 4 9 9 9l1.5-2-3-1.5-1.2 1.2c-1.5-.7-2.8-2-3.5-3.5l1.2-1.2L10.5 7z" fill="#7cc242"/>
            </svg>
            <span>+1 780.555.0184</span>
          </div>
        </div>
        <div class="contact-row">
          <div class="contact-item">
            <svg class="icon" viewBox="0 0 26 26" aria-hidden="true">
              <circle cx="13" cy="13" r="12" fill="none" stroke="#7cc242" stroke-width="2"/>
              <rect x="7" y="9" width="12" height="8" fill="none" stroke="#7cc242" stroke-width="1.6"/>
              <path d="M7 9l6 5 6-5" fill="none" stroke="#7cc242" stroke-width="1.6"/>
            </svg>
            <span>halya.dorosh@quillmail.example</span>
          </div>
          <div class="contact-item">
            <svg class="icon" viewBox="0 0 26 26" aria-hidden="true">
              <circle cx="13" cy="13" r="12" fill="none" stroke="#7cc242" stroke-width="2"/>
              <circle cx="13" cy="13" r="6" fill="none" stroke="#7cc242" stroke-width="1.6"/>
              <path d="M7 13h12M13 7c-2.5 3-2.5 9 0 12M13 7c2.5 3 2.5 9 0 12" fill="none" stroke="#7cc242" stroke-width="1.4"/>
            </svg>
            <span>www.<span class="accent">brovix</span>.example</span>
          </div>
        </div>
      </div>
    </div>

    <div class="address">20517 - 87 Ave. Edmonton, AB, Canada. T6K 4N8</div>
  </div>
</body>
</html>
```